Retail Sign for Houseplant Campaign

Sign will measure 3 to 4 foot tall by 22.2inches and place on rolling racks of houseplants for a retail promotion in The Birchwell Yard. The theme of the promotion will be "New Year, New You!" Selling points which should be on the sign are Houseplants give you a taste of nature, Houseplants boost air quality inside your home, Indoor plants reduce anxiety, Indoor plants make you more productive, Houseplants improve your concentration and memory.
Updates

Target Market(s)

People who love plants

Industry/Entity Type

Horticulture/ retail

Colors
00AB8E
00BBA5
67D7C9
C6EFE9
E9F9F6
59FF00
82FF00
B8FF75
E3FFCB
F4FFEA
FFF300
FFF600
FEFA6F
FFFEC7
FFFEE8

Requirements
Must have
• Must feel energetic and encourage people to buy plants. Should include 1-2 photos and the selling points listed

```html
<!DOCTYPE html>
<html lang="en">
<head>
<meta charset="utf-8">
<title>New Year, New You – Houseplant Sign</title>
<link rel="stylesheet" href="https://fonts.googleapis.com/css2?family=Italiana&family=League+Spartan:wght@700&display=swap">
<style>
  :root {
    --stage: #b6c3a3;
    --paper: #ffffff;
    --leaf-green: #7fb942;
    --palm-green: #4f9a3a;
    --lime-band: #d4dc25;
    --ring: #d8e030;
    --ink-green: #2f6a2c;
    --title-white: #ffffff;
  }
  html, body {
    margin: 0;
    width: 1200px;
    height: 1200px;
    overflow: hidden;
    background: var(--stage);
  }
  .sign {
    position: absolute;
    left: 250px;
    top: 41px;
    width: 710px;
    height: 1133px;
    background: var(--paper);
    transform: scale(0.986);
    transform-origin: top left;
    overflow: hidden;
  }
  .sign__field {
    position: absolute;
    left: 22px;
    top: 20px;
    width: 666px;
    height: 1087px;
    background: var(--leaf-green);
  }
  .sign__palms {
    position: absolute;
    inset: 0;
  }
  .headline {
    position: absolute;
    left: 46px;
    top: 40px;
    margin: 0;
    font-family: "Italiana", serif;
    font-weight: 400;
    font-size: 138px;
    line-height: 136px;
    letter-spacing: 1px;
    color: var(--title-white);
    white-space: nowrap;
  }
  .photo {
    position: absolute;
    border-radius: 50%;
    border: 3px solid var(--ring);
    box-sizing: border-box;
  }
  .photo--care {
    left: 42px; top: 339px; width: 330px; height: 330px;
    background: radial-gradient(circle at 30% 40%, #f1efe9 0%, #dcd6cc 45%, #2f5a32 75%, #1f4424 100%);
  }
  .photo--potting {
    left: 419px; top: 546px; width: 240px; height: 240px;
    background: radial-gradient(circle at 65% 45%, #d7a98a 0%, #efe6dc 40%, #f5f3ee 70%, #e2ddd3 100%);
  }
  .facts {
    position: absolute;
    left: 0;
    top: 810px;
    width: 710px;
    height: 261px;
    background: var(--lime-band);
  }
  .facts__title {
    position: absolute;
    left: 63px;
    top: 24px;
    margin: 0;
    font-family: "Italiana", serif;
    font-weight: 400;
    font-size: 46px;
    line-height: 50px;
    color: var(--title-white);
    white-space: nowrap;
  }
  .facts__list {
    position: absolute;
    left: 54px;
    top: 90px;
    margin: 0;
    padding: 0;
    list-style: none;
    font-family: "League Spartan", sans-serif;
    font-weight: 700;
    font-size: 19px;
    line-height: 31.6px;
    letter-spacing: 0.4px;
    text-transform: uppercase;
    color: var(--ink-green);
  }
  .facts__list li::before {
    content: "• ";
  }
</style>
</head>
<body>
  <main class="sign">
    <div class="sign__field"></div>

    <svg class="sign__palms" width="710" height="1133" viewBox="0 0 710 1133" role="img" aria-label="Decorative palm fronds behind the headline and photos">
      <defs>
        <linearGradient id="frondRight" x1="0" y1="0" x2="1" y2="1">
          <stop offset="0" stop-color="#4f9a3a" stop-opacity="0.15"/>
          <stop offset="1" stop-color="#4f9a3a" stop-opacity="0.55"/>
        </linearGradient>
        <linearGradient id="frondLeft" x1="1" y1="0" x2="0" y2="1">
          <stop offset="0" stop-color="#4f9a3a" stop-opacity="0.1"/>
          <stop offset="1" stop-color="#4f9a3a" stop-opacity="0.5"/>
        </linearGradient>
      </defs>
      <path d="M400 200 C520 180 690 190 710 200 L710 780 L500 810 C450 650 400 450 400 200 Z" fill="url(#frondRight)"/>
      <path d="M0 560 C120 600 260 700 380 810 L0 810 Z" fill="url(#frondLeft)"/>
      <path d="M60 1071 L280 1071 L240 1133 L120 1133 Z" fill="url(#frondLeft)"/>
    </svg>

    <h1 class="headline">NEW YEAR,<br>NEW YOU</h1>

    <div class="photo photo--care" role="img" aria-label="Photo of a smiling woman wiping the leaves of a large monstera plant"></div>
    <div class="photo photo--potting" role="img" aria-label="Photo of a woman tending a croton plant in a woven basket"></div>

    <section class="facts">
      <h2 class="facts__title">DID YOU KNOW?</h2>
      <ul class="facts__list">
        <li>Houseplants give you a taste of nature</li>
        <li>Houseplants improve your concentration &amp; memory</li>
        <li>Houseplants boost air quality inside your home</li>
        <li>Indoor plants make you more productive</li>
        <li>Indoor plants reduce anxiety</li>
      </ul>
    </section>
  </main>
</body>
</html>
```